Business Card for premium dental clinic

We are a premium dental clinic based in Brasov, Romania with more than 15 year on the market, providing quality dental treatment made by a team of more specialized dentists, working with modern equipment as a solution to beautiful and healthy teeth.

Our current logo for the clinic use 2 square with colors black and gold - dr Ternisu - studio, using family fonts Bodoni, Myriad Pro and Segoe Print.
Depending on the printing we used some gold CMYK background or gold foil picture background or a gold gradient.
We want a business card:
- eye catching business card
- distinguished business card
- premium design
- to keep the color scheme of black and gold
- to attract the customers to spent time reading the information
- modern concept

```html
<!DOCTYPE html>
<html lang="en">
<head>
<meta charset="utf-8">
<title>dr Ternisu – Business Card</title>
<link rel="stylesheet" href="https://fonts.googleapis.com/css2?family=Montserrat:wght@400;500;600&display=swap">
<style>
  :root {
    --stage: #2b2725;
    --card-black: #1b1e1e;
    --card-white: #ffffff;
    --gold: #c9a13b;
    --gold-light: #e6d48a;
    --gold-dark: #8a7a34;
    --text-light: #e9e6df;
  }
  * { margin: 0; padding: 0; box-sizing: border-box; }
  html, body {
    width: 1200px; height: 814px; overflow: hidden;
    background: var(--stage);
    font-family: "Montserrat", sans-serif;
  }
  .canvas { position: relative; width: 1200px; height: 814px; }

  .card {
    position: absolute;
    width: 520px; height: 300px;
    border-radius: 4px;
    overflow: hidden;
    box-shadow: 0 18px 40px rgba(0,0,0,.45);
  }

  .brand-name {
    position: absolute;
    left: 50%; transform: translateX(-50%);
    font-weight: 500; color: var(--gold);
    white-space: nowrap;
    letter-spacing: .5px;
  }

  /* Back of card */
  .card-back {
    left: 50px; top: 120px;
    background: var(--card-black);
  }
  .card-back .brand-name { top: 100px; font-size: 36px; }
  .card-back .address {
    position: absolute; left: 0; right: 0; bottom: 56px;
    text-align: center;
    font-size: 13px; color: var(--text-light); letter-spacing: .3px;
  }

  /* Front of card */
  .card-front {
    left: 630px; top: 330px;
    background: var(--card-white);
  }
  .card-front .swoosh { position: absolute; inset: 0; width: 100%; height: 100%; }
  .card-front .brand-name { top: 46px; left: 62%; font-size: 30px; }
  .contact-list {
    position: absolute; left: 26px; top: 172px;
    list-style: none;
    font-size: 13px; color: var(--text-light);
  }
  .contact-list li {
    display: flex; align-items: center; gap: 10px;
    margin-bottom: 8px;
  }
  .contact-list svg { width: 12px; height: 12px; flex: none; }
  .person {
    position: absolute; right: 40px; bottom: 30px;
  }
  .person .name {
    font-size: 19px; font-weight: 600; color: var(--gold);
    letter-spacing: 1px; text-transform: uppercase;
  }
  .person .role {
    font-size: 15px; color: var(--text-light);
  }
</style>
</head>
<body>
<main class="canvas">

  <section class="card card-back" aria-label="Business card back">
    <p class="brand-name">dr Ternisu</p>
    <p class="address">Strada Lungă nr 24, 500035 Brașov</p>
  </section>

  <section class="card card-front" aria-label="Business card front">
    <svg class="swoosh" viewBox="0 0 520 300" preserveAspectRatio="none" aria-hidden="true">
      <defs>
        <linearGradient id="goldBand" x1="0" y1="0" x2="1" y2="0">
          <stop offset="0" stop-color="#8a7a34"/>
          <stop offset=".45" stop-color="#e6d48a"/>
          <stop offset="1" stop-color="#8a7a34"/>
        </linearGradient>
      </defs>
      <path d="M0,58 C70,200 330,228 520,150 L520,300 L0,300 Z" fill="url(#goldBand)"/>
      <path d="M0,82 C80,220 330,246 520,172 L520,300 L0,300 Z" fill="#1b1e1e"/>
    </svg>

    <p class="brand-name">dr Ternisu</p>

    <ul class="contact-list">
      <li>
        <svg viewBox="0 0 24 24" aria-hidden="true"><path fill="#c9a13b" d="M6.6 10.8a15 15 0 0 0 6.6 6.6l2.2-2.2a1 1 0 0 1 1-.25 11.4 11.4 0 0 0 3.6.57 1 1 0 0 1 1 1V20a1 1 0 0 1-1 1A17 17 0 0 1 3 4a1 1 0 0 1 1-1h3.5a1 1 0 0 1 1 1c0 1.25.2 2.45.57 3.6a1 1 0 0 1-.25 1z"/></svg>
        +40 268 555 019
      </li>
      <li>
        <svg viewBox="0 0 24 24" aria-hidden="true"><rect x="2" y="5" width="20" height="14" fill="#c9a13b"/><path d="M4 7l8 6 8-6" fill="none" stroke="#1b1e1e" stroke-width="1.6"/></svg>
        e.marinescu@drternisu.ro
      </li>
      <li>
        <svg viewBox="0 0 24 24" aria-hidden="true"><g fill="none" stroke="#c9a13b" stroke-width="2"><circle cx="12" cy="12" r="9"/><path d="M3 12h18M12 3c3 3 3 15 0 18M12 3c-3 3-3 15 0 18"/></g></svg>
        www.drternisu.ro
      </li>
    </ul>

    <div class="person">
      <p class="name">Elena Marinescu</p>
      <p class="role">Doctor</p>
    </div>
  </section>

</main>
</body>
</html>
```